Flyer für Freie Referentin
I thank Korvam Tepesh for the great work! I’am very satisfied with the design of my flyer, with the arrangement of the photos, the font and the colors. Everything is fine and exactly as I imagined before. All my requested changings were changed very quickly and correctly. I would definitely recommend this designer!
Zielgruppe
Ich biete Vorträge, Kurse, Fortbildungen und Privatunterricht an zu den Themen:
Einführung in die Weltreligionen
und
Feste der Religionen
Außerdem biete ich Führungen durch religiöse Gebäude in Berlin an.
Meine Zielgruppen sind:
1. Pädagogen in Kita, Grund-und Oberschule,
2. Religionslehrer,
3.Fachkräfte im interkulturellen Kontext (Ausländerbehörde, Gesundheitswesen, Sozialwesen) und
4. Menschen, die gern reisen und sich für andere Religionen und Kulturen interessieren
Aufgabenstellung
Ich habe selbst einen 6 seitigen Falzflyer entworfen, mit Text und Bildern und würde diesen inhaltlich weitgehend so lassen, und nur in einem ansprechenden Design umgestalten lassen. Die Fotos, die ich liefere, habe ich in den religiösen Gebäuden selbst gemacht.

```html
<!DOCTYPE html>
<html lang="de">
<head>
<meta charset="utf-8">
<title>Flyer Weltreligionen</title>
<link href="https://fonts.googleapis.com/css2?family=Della+Respira&family=Roboto:wght@400;500;700&display=swap" rel="stylesheet">
<style>
:root{
  --maroon:#8c2129;
  --yellow:#fdd461;
  --orange:#f3a12a;
  --orange-deep:#ec8a2a;
  --white:#ffffff;
  --ink:#1d1d1d;
  --bg:#ececec;
  --head:"Della Respira", Georgia, serif;
  --body:"Roboto", Arial, sans-serif;
}
*{box-sizing:border-box;margin:0;padding:0}
html,body{width:1200px;height:3600px;overflow:hidden;background:var(--bg);font-family:var(--body);color:var(--ink)}
.canvas{position:relative;width:1200px;height:3600px}
.spread{position:absolute;left:60px;width:1080px;height:762px;display:flex;box-shadow:0 6px 24px rgba(0,0,0,.12)}
.spread--outer{top:1010px}
.spread--inner{top:1872px;flex-direction:column;background:var(--white)}
.panel{width:360px;height:100%;position:relative;overflow:hidden}
.ph{display:block}
/* outer panel 1 */
.about{background:linear-gradient(180deg,var(--orange) 0%,var(--orange-deep) 100%)}
.about .portrait{position:absolute;left:40px;top:24px;width:280px;height:372px;border-radius:140px 140px 0 0;background:linear-gradient(180deg,#e9a04f 0%,#6f4d3a 55%,#3d4a3f 100%)}
.about-box{position:absolute;left:18px;right:18px;top:392px;bottom:0;background:var(--maroon);border-radius:26px 26px 0 0;color:var(--white);padding:22px 24px 0}
.about-box .kicker{text-align:center;color:var(--yellow);font-size:16px}
.about-box h2{font-family:var(--head);color:var(--yellow);font-weight:400;font-size:34px;text-align:center;margin:4px 0 16px}
.ticks{list-style:none}
.ticks li{position:relative;padding-left:22px;font-size:14.5px;line-height:1.25;margin-bottom:12px}
.ticks li::before{content:"";position:absolute;left:2px;top:2px;width:6px;height:11px;border:solid var(--tick,var(--yellow));border-width:0 2.4px 2.4px 0;transform:rotate(40deg)}
/* outer panel 2 */
.contact{background:var(--yellow);text-align:center}
.band{background:var(--maroon);color:var(--yellow);font-family:var(--head);font-size:24px;height:36px;line-height:36px}
.contact .band:first-child{margin-top:28px}
.contact h3{font-size:19px;font-weight:500;margin-top:18px}
.contact .role{font-size:14.5px;margin:4px 0 16px}
.contact .addr{font-size:13.5px;line-height:1.35;margin-bottom:14px}
.symbols{font-size:48px;line-height:1;margin:16px auto 10px;width:180px;height:118px;position:relative;color:#111}
.symbols span{position:absolute}
.contact .offer{font-size:14.5px;font-weight:700;line-height:1.3;padding:0 36px}
.pill{background:var(--white);border-radius:14px;margin:18px 42px 0;padding:10px 8px;font-size:14px;line-height:1.3;box-shadow:3px 4px 0 rgba(140,33,41,.25)}
/* outer panel 3 */
.title{background:var(--white)}
.title-head{background:var(--maroon);color:var(--white);text-align:center;height:124px;padding-top:36px}
.title-head .small{font-size:14px;font-weight:700}
.title-head h1{font-family:var(--head);font-weight:400;color:var(--yellow);font-size:31px;margin:4px 0 2px}
.title-head .sub{font-size:15px}
.gallery{position:absolute;left:42px;top:158px;width:276px;display:grid;grid-template-columns:1fr 1fr;gap:10px}
.gallery .ph{border-radius:12px;box-shadow:2px 3px 0 rgba(140,33,41,.35)}
.title-foot{position:absolute;left:0;right:0;bottom:0;height:154px;background:var(--maroon);color:var(--white);text-align:center;padding-top:24px}
.title-foot .religions{font-family:var(--head);color:var(--yellow);font-size:19px;line-height:1.25}
.title-foot p{font-size:14.5px;margin-top:20px;line-height:1.3}
/* inner */
.topband,.bottomband{height:24px;background:var(--maroon);flex:none}
.inner-row{display:flex;height:564px}
.strip{display:flex;height:150px;flex:none}
.strip .ph{flex:1}
.info{padding:22px 22px 0}
.info h2{font-family:var(--head);font-weight:400;color:var(--maroon);font-size:21px;line-height:1.15}
.info h4{font-size:15.5px;font-weight:700;margin:14px 0 8px 12px}
.info .ticks{--tick:var(--maroon);margin-left:14px}
.info .ticks li{font-size:14px;margin-bottom:7px;color:var(--ink)}
.info .plain{font-size:14px;margin:-2px 0 10px 36px;line-height:1.25}
.info .ticks.deep{margin-left:30px}
.info h2.gap{margin-top:18px}
.visits{background:var(--yellow);padding:0}
.visits .txt{padding:22px 28px 0;height:374px}
.visits .txt .ticks{--tick:var(--maroon);margin:14px 0 0}
.visits .txt .ticks li{font-size:14px;margin-bottom:8px}
.visits .fire{height:190px;background:radial-gradient(circle at 50% 55%,#f7b238 0%,#a3521d 35%,#3c3a1c 75%)}
.targets{padding:22px 22px 0}
.targets h2{font-family:var(--head);font-weight:400;color:var(--maroon);font-size:22px}
.targets ol{list-style:none;margin-top:14px}
.targets li{margin-bottom:18px}
.targets .t{color:var(--maroon);font-weight:700;font-size:15.5px;display:flex;gap:10px;line-height:1.2}
.targets p{font-size:14px;line-height:1.25;margin:8px 0 0 24px}
</style>
</head>
<body>
<div class="canvas">

  <section class="spread spread--outer">
    <div class="panel about">
      <div class="portrait ph" role="img" aria-label="Porträtfoto der Referentin vor orangem Hintergrund"></div>
      <div class="about-box">
        <div class="kicker">Über mich:</div>
        <h2>Dr. Mara Bretibbe</h2>
        <ul class="ticks">
          <li>1992-1999 Studium der Religionswissenschaft und Indologie in Berlin</li>
          <li>2008 Dissertation: „Hindus in der deutschen Diaspora.“</li>
          <li>Seit 2000 Wissenschaftliche Referentin für Weltreligionen und Hinduismus</li>
          <li>Seit 2002 Freie Autorin, Schwerpunkt: Religiöse Gruppen in der Diaspora</li>
        </ul>
      </div>
    </div>

    <div class="panel contact">
      <div class="band">Kontakt</div>
      <h3>Dr. Mara Bretibbe</h3>
      <div class="role">Religionswissenschaftlerin und Indologin</div>
      <div class="addr"><b>Büro :</b><br>Lindenhofstraße 22 10178 Berlin<br><b>Tel. :</b> 030 55501234<br><b>Mobil :</b> 01765550219<br>info@mabretibbe.de<br>www.mabretibbe.de</div>
      <div class="band">Mehr Infos &amp; Buchung</div>
      <div class="symbols" aria-label="Symbole der Weltreligionen">
        <span style="left:66px;top:0">✡</span>
        <span style="left:0;top:30px">✝</span>
        <span style="left:116px;top:28px">☪</span>
        <span style="left:38px;top:64px">ॐ</span>
        <span style="left:96px;top:66px">☸</span>
      </div>
      <p class="offer">Ich biete Seminare für Einzelpersonen, Bildungseinrichtungen und Teams an – in meinem Büro oder vor Ort.</p>
      <div class="pill">Aktuelle Preise und Konditionen finden Sie auf meiner Website.<br>www.mabretibbe.de</div>
      <div class="pill">Individuelle Angebote – Preise auf Nachfrage unter: info@mabretibbe.de oder :Tel.: 03(0) 55501 234</div>
    </div>

    <div class="panel title">
      <div class="title-head">
        <div class="small">Weltreligionen in Berlin erleben</div>
        <h1>Vorträge &amp; Seminare</h1>
        <div class="sub">Führungen &amp; Privatunterricht in Berlin</div>
      </div>
      <div class="gallery">
        <div class="ph" style="height:126px;background:linear-gradient(160deg,#b9c3c8,#8a5a3c)" role="img" aria-label="Foto einer religiösen Prozession"></div>
        <div class="ph" style="height:126px;background:linear-gradient(160deg,#2e4f73,#b9462e)" role="img" aria-label="Foto einer festlichen Zeremonie"></div>
        <div class="ph" style="height:274px;grid-row:span 2;background:linear-gradient(170deg,#5f8a3c,#d6a13a 60%,#7a3a2a)" role="img" aria-label="Foto eines Straßenfestes mit Tänzerinnen"></div>
        <div class="ph" style="height:132px;background:linear-gradient(160deg,#c98a2c,#e06a1e)" role="img" aria-label="Foto buddhistischer Mönche"></div>
        <div class="ph" style="height:132px;background:linear-gradient(160deg,#c9b79a,#3c3f52)" role="img" aria-label="Foto eines Mannes mit Gebetsschal"></div>
      </div>
      <div class="title-foot">
        <div class="religions">Judentum - Christentum - Islam<br>Hinduismus - Buddhismus</div>
        <p>Lernen Sie die Weltreligionen kennen und verstehen!</p>
      </div>
    </div>
  </section>

  <section class="spread spread--inner">
    <div class="topband"></div>
    <div class="inner-row">
      <div class="panel info">
        <h2>Weltreligionen verstehen –<br>Menschen besser begegnen</h2>
        <h4>Mein Angebot:</h4>
        <ul class="ticks">
          <li>Vorträge &amp; Seminare zu: Judentum, Christentum, Islam, Hinduismus und Buddhismus</li>
          <li>Vorträge &amp; Seminare zu religiösen Festen und Traditionen</li>
          <li>Besuche religiöser Stätten</li>
        </ul>
        <p class="plain">Individuelle Weiterbildungen &amp; Privatunterricht</p>
        <h2 class="gap">Welche Themen biete ich an?</h2>
        <h4 style="margin-left:0">1. Einführung Weltreligionen</h4>
        <ul class="ticks deep">
          <li>Herkunft &amp; Heilige Schrift</li>
          <li>Lehren &amp; Rituale</li>
          <li>Ethik &amp; Verhalten</li>
        </ul>
        <h4 style="margin-left:0">2. Feste in den Religionen</h4>
        <ul class="ticks deep">
          <li>Kalender &amp; Anlässe</li>
          <li>Geschichten &amp; Musik</li>
          <li>Rituale &amp; Speisen</li>
        </ul>
      </div>
      <div class="panel visits">
        <div class="txt info" style="padding:22px 28px 0">
          <h2>Besuche religiöser Stätten</h2>
          <ul class="ticks">
            <li>Führung durch die Räume</li>
            <li>Teilnahme an Zeremonien</li>
            <li>Austausch mit Gläubigen</li>
          </ul>
          <h2 class="gap">Was Sie mitnehmen:</h2>
          <ul class="ticks">
            <li>Klar verständliches Wissen zu den Weltreligionen</li>
            <li>Hintergründe zu Festen, Bräuchen und Symbolen</li>
            <li>Aha-Momente für Beruf, Alltag und Reisen</li>
          </ul>
        </div>
        <div class="fire ph" role="img" aria-label="Foto einer Feuerschale bei einem Ritual"></div>
      </div>
      <div class="panel targets">
        <h2>Meine Angebote richten sich an:</h2>
        <ol>
          <li><div class="t"><span>1.</span><span>Lehrkräfte allgemein:</span></div>
            <p>Gewinnen Sie fundiertes Wissen, um <b>Schüler•innen unterschiedlicher Herkunft</b> besser zu begleiten</p></li>
          <li><div class="t"><span>2.</span><span>Religionslehrerinnen und Religionslehrer:</span></div>
            <p>Vertiefen Sie Ihr Wissen zu Inhalten der großen Religionen – praxisnah und aktuell!</p></li>
          <li><div class="t"><span>3.</span><span>Fachkräfte im interkulturellen Kontext</span></div>
            <p>(Ausländerbehörde, Asylberatung, Gesundheitswesen)</p>
            <p>Gewinnen Sie Sicherheit im Umgang mit religiös geprägten Verhaltensweisen!</p></li>
          <li><div class="t"><span>4.</span><span>Reisefreudige &amp; Neugierige:</span></div>
            <p>Entdecken Sie spannende Einblicke in Rituale, Werte und Feiertage weltweit!</p></li>
        </ol>
      </div>
    </div>
    <div class="strip">
      <div class="ph" style="background:linear-gradient(160deg,#7c6a5a,#3a2c24)" role="img" aria-label="Foto eines Bücherregals mit heiligen Schriften"></div>
      <div class="ph" style="background:linear-gradient(160deg,#6f8fb4,#8c4a5a)" role="img" aria-label="Foto einer Gruppe bei einem Fest im Freien"></div>
      <div class="ph" style="background:linear-gradient(160deg,#8a2a2a,#d9b14c)" role="img" aria-label="Foto festlicher Speisen und Opfergaben"></div>
      <div class="ph" style="background:linear-gradient(180deg,#4a74b8,#e2c25a)" role="img" aria-label="Foto eines goldenen Tempelturms"></div>
      <div class="ph" style="background:linear-gradient(160deg,#bfc1c4,#5a5a5a)" role="img" aria-label="Foto einer Menschenmenge bei einer Feier"></div>
      <div class="ph" style="background:linear-gradient(160deg,#8fb3c6,#3f5a6a)" role="img" aria-label="Foto eines Moscheeinnenraums"></div>
    </div>
    <div class="bottomband"></div>
  </section>

</div>
</body>
</html>
```